DL Cards to get buyers attention

I’m looking to have four double-sided DL flyers professionally prepared and made print-ready in high resolution.

I have uploaded the four existing designs, and I’m happy for them to be reviewed with a fresh set of eyes. While I’m generally happy with the direction, I’m very open to recommendations around layout, typography, imagery, colour balance, spacing and overall presentation if there are opportunities to create a stronger and more professional result.

The key objective is to develop a consistent and recognisable suite of marketing material that strengthens both Lon Pakard brand awareness and my personal profile in the local real estate market. Each flyer should feel like part of the same campaign while still having its own clear message and purpose.

I want the finished designs to feel professional, confident, modern and premium, without becoming overly busy or losing the simplicity that makes a DL flyer easy to read. Strong headlines, clear messaging and an obvious call to action are important. The Lon Pakard branding should be immediately recognisable, while my photograph, name and contact details should be incorporated naturally and consistently.

Please review the existing designs and suggest any changes that would improve their visual impact, readability and consistency. I’m also open to seeing an alternative design direction if you believe there is a better overall look.

The final artwork needs to be supplied professionally print-ready at DL size (210 mm × 99 mm), double-sided, high resolution, CMYK where appropriate, with 3 mm bleed and safe margins, so it can be provided directly to a commercial printer.

The overall goal is simple: strong branding, professional presentation, consistent recognition and marketing material that people will remember.

Target Market(s)

People looking at selling their homes

Industry/Entity Type

Real Estate

Font styles to use
Serif
Sans Serif

Requirements
Must have
• Strong brand awareness - Lon Pakard
Nice to have
• bright and fresh

```html
<!DOCTYPE html>
<html lang="en">
<head>
<meta charset="utf-8">
<title>Lon Pakard DL Flyer Suite</title>
<link rel="stylesheet" href="https://fonts.googleapis.com/css2?family=Great+Vibes&family=Lato:wght@400;700;900&family=Playfair+Display:wght@700;900&display=swap">
<style>
:root{
  --navy:#2d2f92;
  --navy-deep:#23257a;
  --yellow:#ffe900;
  --board:#5d5d5d;
  --ink:#3a3a3a;
  --grey:#f0f0f2;
  --grey-2:#e4e4e8;
  --dark:#333335;
  --white:#ffffff;
}
*{box-sizing:border-box;margin:0;padding:0}
html,body{width:1200px;height:1191px;overflow:hidden}
body{background:var(--board);font-family:'Lato',sans-serif;color:var(--ink);position:relative}
.serif{font-family:'Playfair Display',serif}
.script{font-family:'Great Vibes',cursive;font-weight:400;line-height:1;white-space:nowrap}
.file-label{position:absolute;width:500px;text-align:center;color:#f2f2f2;font-size:17px;letter-spacing:.5px;font-family:'Lato',sans-serif}
.card{position:absolute;width:500px;height:236px;overflow:hidden;background:var(--white)}
.abs{position:absolute}
.photo{position:absolute}
.brand-tab{position:absolute;top:0;background:var(--yellow);display:flex;align-items:flex-end;justify-content:center;padding-bottom:10px}
.brand-name{font-family:'Lato',sans-serif;font-weight:900;color:var(--navy);font-size:11px;white-space:nowrap}
.lead{position:absolute;border-left:2px solid var(--yellow);padding-left:7px;font-size:9.6px;line-height:1.15}
.icon-box{position:absolute;width:24px;height:24px;background:var(--yellow);border-bottom:2px solid var(--navy);display:flex;align-items:center;justify-content:center}
.icon-box svg{width:15px;height:15px}
.tip h4{font-size:7.6px;font-weight:700;color:#2a2a2a;text-transform:uppercase}
.tip p{font-size:6.9px;line-height:1.2;color:#555}
.phone-dot{display:inline-flex;width:18px;height:18px;border-radius:50%;align-items:center;justify-content:center;flex:none}
.phone-dot svg{width:11px;height:11px}
.steps-col{position:absolute;top:0;height:181px}
.step-head{position:absolute;top:8px;left:0;right:0;height:26px;background:var(--yellow);display:flex;align-items:center;padding-left:10px;gap:4px}
.step-num{font-family:'Lato',sans-serif;font-weight:900;color:var(--navy);font-size:19px;line-height:1;border-right:1.5px solid var(--navy);padding-right:4px}
.step-title{font-weight:900;color:var(--navy);font-size:7px;line-height:1.05}
.step-body{position:absolute;top:42px;left:12px;right:6px;font-size:5.3px;line-height:1.3;color:#555}
.step-body p{margin-bottom:5px}
.step-body b{color:#222}
.value-row{display:flex;align-items:center;gap:5px;font-weight:700;color:var(--navy);font-size:8px}
.value-row svg{width:11px;height:11px}
.list-row{position:absolute;left:0;width:118px;height:32px;display:flex;align-items:center}
.list-row svg{width:22px;height:22px;margin:0 8px 0 12px;flex:none}
.list-row span{border-left:1px solid var(--navy);padding-left:5px;font-size:9.2px;line-height:1.1;color:#333}
.report-item{position:absolute;left:0;width:160px;display:flex;gap:14px}
.report-item h5{font-size:7.4px;font-weight:900;color:var(--navy)}
.report-item p{font-size:7px;line-height:1.25;color:#666}
.note-col{position:absolute;top:12px;width:145px;font-size:6.3px;line-height:1.3;color:#555}
.note-col h5{font-size:6.8px;font-weight:700;color:#222;line-height:1.15}
.note-col h5.num-head{display:flex;align-items:flex-start}
.num-sq{display:inline-flex;width:14px;height:14px;background:var(--yellow);border:1px solid var(--navy);color:var(--navy);font-weight:900;font-size:10px;align-items:center;justify-content:center;margin-right:5px;flex:none}
.callout{border:1px solid var(--yellow);border-radius:3px;display:flex;gap:6px;padding:4px 5px;margin-top:4px}
.callout svg{width:16px;height:16px;flex:none;align-self:center}
</style>
</head>
<body>
<svg width="0" height="0" style="position:absolute">
  <defs>
    <symbol id="phone" viewBox="0 0 16 16"><path d="M4.5 1.5c1 0 2.3 2.6 2.3 3.4 0 .9-1.2 1.2-1.2 2 0 1.2 2.3 3.5 3.5 3.5.8 0 1.1-1.2 2-1.2.8 0 3.4 1.3 3.4 2.3 0 1.1-1.4 2.5-2.8 2.5C7.2 14 2 8.8 2 4.3 2 2.9 3.4 1.5 4.5 1.5z" fill="currentColor"/></symbol>
    <symbol id="house" viewBox="0 0 16 16"><path d="M2 8 8 3l6 5M4 7v6h8V7" fill="none" stroke="currentColor" stroke-width="1.4" stroke-linejoin="round"/><rect x="7" y="9.5" width="2" height="3.5" fill="currentColor"/></symbol>
    <symbol id="tick" viewBox="0 0 16 16"><path d="M3 8.5l3 3 7-7" fill="none" stroke="currentColor" stroke-width="1.8" stroke-linecap="round" stroke-linejoin="round"/></symbol>
    <symbol id="pin" viewBox="0 0 16 16"><path d="M8 1.5a4.5 4.5 0 0 1 4.5 4.5C12.5 9.5 8 14.5 8 14.5S3.5 9.5 3.5 6A4.5 4.5 0 0 1 8 1.5z" fill="none" stroke="currentColor" stroke-width="1.4"/><circle cx="8" cy="6" r="1.6" fill="currentColor"/></symbol>
    <symbol id="doc" viewBox="0 0 16 16"><path d="M4 1.5h6l3 3v10H4z" fill="none" stroke="currentColor" stroke-width="1.4" stroke-linejoin="round"/><path d="M6 7h5M6 9.5h5M6 12h3" stroke="currentColor" stroke-width="1.2"/></symbol>
    <symbol id="bars" viewBox="0 0 16 16"><path d="M3 14V10M6.5 14V7M10 14V5M13.5 14V2" stroke="currentColor" stroke-width="2"/></symbol>
    <symbol id="heart" viewBox="0 0 16 16"><path d="M8 14S2 10 2 5.8A3 3 0 0 1 8 4.5a3 3 0 0 1 6 1.3C14 10 8 14 8 14z" fill="none" stroke="currentColor" stroke-width="1.4"/></symbol>
    <symbol id="star" viewBox="0 0 16 16"><path d="M8 1.5l1.9 4 4.4.5-3.3 3 .9 4.4L8 11.2l-3.9 2.2.9-4.4-3.3-3 4.4-.5z" fill="none" stroke="currentColor" stroke-width="1.3" stroke-linejoin="round"/></symbol>
  </defs>
</svg>

<div class="file-label" style="left:77px;top:34px">Lon-Pakard-DL-Flyer-1</div>
<div class="file-label" style="left:628px;top:34px">Lon-Pakard-DL-Flyer-2</div>
<div class="file-label" style="left:77px;top:608px">Lon-Pakard-DL-Flyer-3</div>
<div class="file-label" style="left:628px;top:608px">Lon-Pakard-DL-Flyer-4</div>

<!-- Flyer 1 front -->
<section class="card flyer-one-front" style="left:77px;top:77px">
  <div class="photo" role="img" aria-label="Beachfront villa terrace with sand path and ocean under a blue sky" style="inset:0;background:linear-gradient(180deg,#3f56b0 0%,#5c86d4 35%,#9cc3e6 52%,#dccbb0 70%,#b9b1a5 100%)"></div>
  <div class="abs" style="inset:0;background:linear-gradient(90deg,rgba(45,47,146,.95) 0%,rgba(45,47,146,.8) 40%,rgba(45,47,146,0) 60%);height:120px"></div>
  <div class="abs" style="right:0;top:0;width:170px;height:236px;background:linear-gradient(180deg,#b8573c,#c9714f 60%,#6f9a4d)" role="img" aria-label="Terracotta villa facade with pergola"></div>
  <div class="abs serif" style="left:13px;top:10px;font-size:35px;font-weight:900;color:var(--white);line-height:1">10 THINGS</div>
  <div class="abs serif" style="left:13px;top:46px;font-size:15.5px;font-weight:700;color:var(--yellow);line-height:1.1">TO GET YOUR PROPERTY</div>
  <div class="abs script" style="left:28px;top:74px;font-size:28px;color:var(--white);transform:rotate(-6deg);transform-origin:left center">Ready to Sell</div>
  <div class="abs" style="left:28px;top:104px;width:100px;height:3px;background:var(--yellow);border-radius:2px;transform:rotate(-6deg);transform-origin:left center"></div>
  <div class="brand-tab" style="left:243px;width:69px;height:65px"><span class="brand-name" style="font-size:9.5px">Lon Pakard</span></div>
  <p class="lead" style="left:14px;top:152px;color:#2c2c2c">A well-prepared home makes<br>a lasting first impression and helps<br>achieve the best result.</p>
</section>

<!-- Flyer 1 back -->
<section class="card flyer-one-back" style="left:77px;top:333px;background:var(--grey)">
  <div class="abs" style="left:394px;top:0;width:76px;height:236px;background:repeating-linear-gradient(90deg,var(--yellow) 0 12px,#fff04d 12px 20px)"></div>
  <div class="photo" role="img" aria-label="Portrait of agent Dane in a white shirt" style="left:382px;top:42px;width:118px;height:194px;background:linear-gradient(180deg,#c99c80 0%,#c99c80 32%,#f4f4f4 36%,#e6e6e6 100%);border-radius:50px 50px 0 0"></div>

  <div class="icon-box" style="left:12px;top:12px"><svg style="color:var(--navy)"><use href="#star"/></svg></div>
  <div class="abs tip" style="left:42px;top:10px;width:170px"><h4>1.Clean &amp; Declutter</h4><p>Remove personal items and clutter. A clean, tidy home feels bigger, brighter and more inviting.</p></div>
  <div class="icon-box" style="left:12px;top:49px"><svg style="color:var(--navy)"><use href="#house"/></svg></div>
  <div class="abs tip" style="left:42px;top:47px;width:170px"><h4>2.Finish Projects &amp; Repairs</h4><p>Fix minor issues, leaky taps, loose handles and any repairs buyers will notice.</p></div>
  <div class="icon-box" style="left:12px;top:88px"><svg style="color:var(--navy)"><use href="#doc"/></svg></div>
  <div class="abs tip" style="left:42px;top:86px;width:170px"><h4>3.Do a Thorough Inspection</h4><p>Check the big and small things – inside and out – so there are no surprises later.</p></div>
  <div class="icon-box" style="left:12px;top:124px"><svg style="color:var(--navy)"><use href="#tick"/></svg></div>
  <div class="abs tip" style="left:42px;top:122px;width:170px"><h4>4.Paint</h4><p>A fresh coat of neutral paint can transform your home and make it feel well maintained.</p></div>
  <div class="icon-box" style="left:12px;top:162px"><svg style="color:var(--navy)"><use href="#star"/></svg></div>
  <div class="abs tip" style="left:42px;top:160px;width:170px"><h4>5.Freshen up Fixtures &amp; Hardware</h4><p>Update old light fittings, tapware and cabinet handles for an instant lift.</p></div>

  <div class="icon-box" style="left:209px;top:12px"><svg style="color:var(--navy)"><use href="#house"/></svg></div>
  <div class="abs tip" style="left:239px;top:10px;width:150px"><h4>6.Clean or Replace Flooring</h4><p>Clean carpets, tiles and floors or replace if needed. Great floors make a big difference.</p></div>
  <div class="icon-box" style="left:209px;top:49px"><svg style="color:var(--navy)"><use href="#house"/></svg></div>
  <div class="abs tip" style="left:239px;top:47px;width:150px"><h4>7.Create a Welcoming Entrance</h4><p>Tidy up the front yard, clean the entry and add plants for great street appeal.</p></div>
  <div class="icon-box" style="left:209px;top:88px"><svg style="color:var(--navy)"><use href="#star"/></svg></div>
  <div class="abs tip" style="left:239px;top:86px;width:150px"><h4>8.Stage Your Home</h4><p>Arrange furniture to showcase space and lifestyle. Less is more when selling.</p></div>
  <div class="icon-box" style="left:209px;top:124px"><svg style="color:var(--navy)"><use href="#tick"/></svg></div>
  <div class="abs tip" style="left:239px;top:122px;width:150px"><h4>9.Eliminate Odours</h4><p>Remove pet smells, smoke, cooking and musty odours for a fresh, neutral home.</p></div>
  <div class="icon-box" style="left:209px;top:162px"><svg style="color:var(--navy)"><use href="#bars"/></svg></div>
  <div class="abs tip" style="left:239px;top:160px;width:150px"><h4>10.Get Your Real Price</h4><p>Work with an agent to set the right price and attract the right buyers.</p></div>

  <div class="abs script" style="left:12px;top:206px;font-size:18px;color:#333">Call Dane</div>
  <div class="abs" style="left:86px;top:204px;width:121px;height:20px;background:var(--yellow);border-radius:10px;display:flex;align-items:center;gap:8px;padding-left:3px">
    <span class="phone-dot" style="background:var(--dark);color:var(--yellow)"><svg><use href="#phone"/></svg></span>
    <span style="font-weight:900;font-size:12px;color:#222">0491 570 156</span>
  </div>
  <div class="abs" style="left:207px;top:204px;width:175px;height:20px;background:var(--navy);color:var(--yellow);font-weight:900;font-size:10px;display:flex;align-items:center;justify-content:center">YOUR PROPERTY OUR PRIORITY</div>
</section>

<!-- Flyer 2 front -->
<section class="card flyer-two-front" style="left:628px;top:77px">
  <div class="photo" role="img" aria-label="Timber boardwalk stairs leading through dunes to the ocean" style="inset:0;background:linear-gradient(180deg,#2d2f92 0%,#3a4da8 30%,#87b7db 48%,#c9dde6 58%,#b49a6c 78%,#8a6b3e 100%)"></div>
  <div class="abs" style="right:0;top:0;width:100px;height:236px;background:linear-gradient(180deg,#fff7c2,#f2e27a 50%,#d8b040)" role="img" aria-label="Sunlit dune grasses"></div>
  <div class="abs" style="left:57px;top:14px;white-space:nowrap">
    <span class="serif" style="font-size:31px;font-weight:900;color:var(--yellow)">STEPS OF A</span><span class="script" style="font-size:50px;color:var(--white);margin-left:-6px;position:relative;top:6px">Sale</span>
  </div>
  <p class="lead" style="left:70px;top:75px;color:var(--white);font-size:9.4px">A clear process. Proven results. From listing to settlement,<br>I'm with you every step of the way.</p>
  <div class="brand-tab" style="left:400px;width:88px;height:70px"><span class="brand-name">Lon Pakard</span></div>
</section>

<!-- Flyer 2 back -->
<section class="card flyer-two-back" style="left:628px;top:333px;background:var(--grey)">
  <div class="steps-col" style="left:0;width:122px;background:var(--grey-2)">
    <div class="step-head"><span class="step-num">1</span><span class="step-title">PREPARATION<br>&amp; APPRAISAL</span></div>
    <div class="step-body">
      <p><b>Agent selection</b> -Choose a local agent and set a realistic selling price based on market research.</p>
      <p><b>Home styling</b> -Clean, declutter, and repair flaws to make the property photogenic. Ask your agent for staging tips to help present the home at its best.</p>
      <p><b>Contract preparation</b> -Work with a solicitor or conveyancer to prepare the contract of sale and vendor statement.</p>
      <p><b>LON PAKARD TIP:</b> -Good preparation can make a big difference to how buyers see your property.</p>
    </div>
  </div>
  <div class="steps-col" style="left:122px;width:109px;background:var(--grey)">
    <div class="step-head"><span class="step-num">2</span><span class="step-title">CHOOSING A<br>METHOD OF SALE</span></div>
    <div class="step-body">
      <p><b>Auction</b> -Set a date, market without a price to build urgency, and encourage competitive bidding.</p>
      <p><b>Private Treaty</b> -List an asking price and negotiate individual offers with buyers.</p>
      <p><b>Expressions of Interest / Tender</b> -Invite confidential offers by a set date for unique properties.</p>
      <p><b>LON PAKARD TIP:</b> -The right method depends on your property, the local market and your goals. Your agent can recommend the best strategy.</p>
    </div>
  </div>
  <div class="steps-col" style="left:231px;width:123px;background:var(--grey-2)">
    <div class="step-head"><span class="step-num">3</span><span class="step-title">MARKETING<br>&amp; CAMPAIGN</span></div>
    <div class="step-body">
      <p><b>Launch your campaign</b> -Present your property to the market with professional photography, online advertising, signage and targeted promotion.</p>
      <p><b>Inspections</b> -Hold open homes and private viewings to give buyers the chance to experience your property.</p>
      <p><b>Vendor reports</b> -Receive regular updates covering buyer feedback, inspection numbers, enquiry levels and market interest.</p>
      <p><b>LON PAKARD TIP:</b> -A strong campaign builds buyer interest and competition.</p>
    </div>
  </div>
  <div class="steps-col" style="left:354px;width:146px;background:var(--grey)">
    <div class="step-head"><span class="step-num">4</span><span class="step-title">CONTRACT EXCHANGE<br>&amp; SETTLEMENT</span></div>
    <div class="step-body">
      <p><b>Exchange</b> -Both buyer and seller sign separate copies of the contract, and they are swapped.</p>
      <p><b>Deposit</b> -The buyer pays a deposit, usually 10%, which is held in a trust account.</p>
      <p><b>Cooling-off</b> -Private treaty sales usually include a 5-day cooling-off period for buyers (none at auction).</p>
      <p><b>Settlement</b> -The final transaction is completed, typically 42 days after exchange, and keys are handed over.</p>
      <p><b>LON PAKARD TIP:</b> -Your agent and solicitor will guide you through to key handover.</p>
    </div>
  </div>
  <div class="abs" style="left:0;top:181px;width:122px;height:55px;background:var(--dark);color:var(--white);font-size:6.3px;font-weight:700;line-height:1.3;padding:14px 12px">If you are thinking of selling, planning to sell or would simply like to chat about your options..</div>
  <div class="abs" style="left:122px;top:181px;width:268px;height:55px;background:var(--navy)"></div>
  <div class="abs" style="left:138px;top:186px;color:var(--yellow);font-weight:700;font-size:9.5px">Reach out and call me today.</div>
  <div class="abs script" style="left:138px;top:203px;color:var(--white);font-size:24px">Dane</div>
  <div class="abs" style="left:200px;top:206px;display:flex;align-items:center;gap:8px">
    <span class="phone-dot" style="background:var(--yellow);color:var(--navy)"><svg><use href="#phone"/></svg></span>
    <span style="color:var(--white);font-weight:900;font-size:15px">0491 570 156</span>
  </div>
  <div class="photo" role="img" aria-label="Portrait of agent Dane" style="left:332px;top:155px;width:56px;height:81px;background:linear-gradient(180deg,#c99c80 0%,#c99c80 34%,#f2f2f2 38%,#e4e4e4);border-radius:26px 26px 0 0"></div>
  <div class="abs" style="left:390px;top:181px;width:110px;height:55px;background:var(--yellow);padding:7px 0 0 10px;display:flex;flex-direction:column;gap:3px">
    <div class="value-row"><svg><use href="#pin"/></svg>Local Knowledge</div>
    <div class="value-row"><svg><use href="#star"/></svg>Exceptional Service</div>
    <div class="value-row"><svg><use href="#heart"/></svg>Genuine Care</div>
  </div>
</section>

<!-- Flyer 3 front -->
<section class="card flyer-three-front" style="left:77px;top:646px">
  <div class="photo" role="img" aria-label="Tropical beach with palm fronds, rocks and turquoise water" style="inset:0;background:linear-gradient(180deg,#ffffff 0%,#eef6fb 30%,#9fd0ec 55%,#7ec3dd 70%,#f1ece2 88%,#ffffff 100%)"></div>
  <div class="photo" role="img" aria-label="Portrait of agent Dane smiling in a white shirt" style="left:170px;top:38px;width:175px;height:198px;background:linear-gradient(180deg,#c99c80 0%,#c99c80 40%,#f5f5f5 44%,#e6e6e6 100%);border-radius:70px 70px 0 0"></div>
  <div class="abs serif" style="left:13px;top:11px;font-size:20.5px;font-weight:900;color:var(--navy);line-height:1">The smart<br>way to sell<br>your property</div>
  <div class="abs script" style="left:13px;top:80px;font-size:24px;color:var(--navy);line-height:1.05;transform:rotate(-5deg);white-space:normal">Start with<br>knowledge.</div>
  <p class="lead" style="left:14px;top:156px;color:#333">Inspect your property before<br>you sell and give buyers<br>confidence from day one.</p>
  <div class="brand-tab" style="left:413px;width:75px;height:68px"><span class="brand-name" style="font-size:10px">Lon Pakard</span></div>
  <div class="list-row" style="left:382px;top:92px;background:rgba(255,255,255,.85)"><svg style="color:var(--navy)"><use href="#house"/></svg><span>Know what<br>needs attention</span></div>
  <div class="list-row" style="left:382px;top:126px;background:rgba(236,236,240,.9)"><svg style="color:var(--navy)"><use href="#tick"/></svg><span>Fix issues and<br>improve value</span></div>
  <div class="list-row" style="left:382px;top:159px;background:rgba(255,255,255,.85)"><svg style="color:var(--navy)"><use href="#house"/></svg><span>Build buyer<br>confidence</span></div>
  <div class="list-row" style="left:382px;top:192px;background:rgba(236,236,240,.9)"><svg style="color:var(--navy)"><use href="#bars"/></svg><span>Market with<br>confidence</span></div>
  <div class="abs" style="left:0;top:208px;width:382px;height:28px;background:linear-gradient(90deg,var(--yellow) 70%,rgba(255,233,0,0));color:var(--navy);font-weight:700;font-size:9.4px;display:flex;align-items:center;padding-left:13px">Your property. Our priority. | Let’s achieve your next move together.</div>
</section>

<!-- Flyer 3 back -->
<section class="card flyer-three-back" style="left:77px;top:902px">
  <div class="abs" style="left:0;top:0;width:180px;height:198px;background:var(--grey)"></div>
  <div class="abs" style="left:180px;top:0;width:160px;height:198px;background:#e9e9ec"></div>
  <div class="abs" style="left:180px;top:0;width:320px;height:19px;background:linear-gradient(90deg,var(--navy),#c9cbe8 85%,#f2f2f8)"></div>
  <div class="abs serif" style="left:13px;top:12px;font-size:20.5px;font-weight:900;color:var(--navy);line-height:1">PROPERTY<br>REPORT</div>
  <div class="abs" style="left:13px;top:80px;font-weight:700;font-size:11px;color:#333;line-height:1.05">What’s in the Lon Pakard<br>property report?</div>
  <p class="abs" style="left:13px;top:114px;width:150px;font-size:7.2px;line-height:1.3;color:#666">The Lon Pakard Property Report gives you an in-depth understanding of your property and the market with comprehensive data including property value estimates, comparable sales and historical suburb performance.</p>
  <div class="report-item" style="left:180px;top:45px"><div class="icon-box" style="position:static;flex:none"><svg style="color:var(--navy)"><use href="#house"/></svg></div><div><h5>IN-DEPTH ANALYSIS</h5><p>Comprehensive insights<br>into your property.</p></div></div>
  <div class="report-item" style="left:180px;top:94px"><div class="icon-box" style="position:static;flex:none"><svg style="color:var(--navy)"><use href="#bars"/></svg></div><div><h5>MARKET DATA</h5><p>Up-to-date local market<br>trends and performance.</p></div></div>
  <div class="report-item" style="left:180px;top:143px"><div class="icon-box" style="position:static;flex:none"><svg style="color:var(--navy)"><use href="#doc"/></svg></div><div><h5>CLEAR REPORT</h5><p>Easy to understand,<br>well-presented report.</p></div></div>
  <div class="abs script" style="left:340px;top:42px;width:160px;text-align:center;font-size:16px;line-height:1.2;color:var(--navy);white-space:normal">Want to know<br>what your property<br>could be worth?</div>
  <div class="abs" style="left:380px;top:106px;width:85px;height:2px;background:var(--yellow);transform:rotate(-5deg)"></div>
  <div class="abs serif" style="left:340px;top:123px;width:160px;text-align:center;font-size:13.5px;font-weight:900;color:var(--navy)">Call Dane</div>
  <div class="abs" style="left:354px;top:151px;width:146px;height:19px;background:var(--dark);border-radius:10px 0 0 10px;display:flex;align-items:center;gap:10px;padding-left:3px">
    <span class="phone-dot" style="background:var(--yellow);color:var(--dark)"><svg><use href="#phone"/></svg></span>
    <span style="color:var(--white);font-weight:900;font-size:12px">0491 570 156</span>
  </div>
  <div class="abs" style="left:0;top:198px;width:500px;height:38px;background:var(--yellow);display:flex;align-items:center;justify-content:center;gap:22px">
    <div class="value-row" style="font-size:13px"><svg style="width:16px;height:16px"><use href="#pin"/></svg>Local Knowledge</div>
    <div class="value-row" style="font-size:13px"><svg style="width:16px;height:16px"><use href="#star"/></svg>Exceptional Service</div>
    <div class="value-row" style="font-size:13px"><svg style="width:16px;height:16px"><use href="#heart"/></svg>Genuine Care</div>
  </div>
</section>

<!-- Flyer 4 front -->
<section class="card flyer-four-front" style="left:628px;top:646px">
  <div class="photo" role="img" aria-label="Tropical bay with palm trees, jetty and turquoise water" style="inset:0;background:linear-gradient(100deg,#ffffff 0%,#ffffff 30%,#c8e6f6 50%,#7fc4e6 70%,#3f9fd6 100%)"></div>
  <div class="abs" style="left:200px;top:140px;width:300px;height:58px;background:linear-gradient(180deg,#4f8d4a,#7ccfcf 55%,#e8f2ea)" role="img" aria-label="Green headland and shallow lagoon"></div>
  <div class="photo" role="img" aria-label="Portrait of agent Dane smiling in a white shirt" style="left:287px;top:30px;width:140px;height:168px;background:linear-gradient(180deg,#c99c80 0%,#c99c80 44%,#f5f5f5 48%,#e6e6e6 100%);border-radius:60px 60px 0 0"></div>
  <div class="abs serif" style="left:13px;top:12px;font-size:21px;font-weight:900;color:var(--navy);line-height:1">IS YOUR<br>PROPERTY<br>READY TO SELL?</div>
  <div class="abs" style="left:13px;top:81px;width:85px;height:3px;background:var(--yellow);transform:rotate(-3deg)"></div>
  <div class="abs" style="left:13px;top:96px;font-size:10px;color:#333">Local knowledge. <b>Exceptional service.</b></div>
  <div class="abs" style="left:13px;top:134px;display:flex;gap:8px;align-items:center"><svg style="width:20px;height:20px;color:var(--navy)"><use href="#pin"/></svg><div><div style="font-weight:900;color:var(--navy);font-size:7.8px">LOCAL KNOWLEDGE</div><div style="font-size:7.4px;color:#666">We know the area.</div></div></div>
  <div class="abs" style="left:13px;top:163px;display:flex;gap:8px;align-items:center"><svg style="width:20px;height:20px;color:var(--navy)"><use href="#star"/></svg><div><div style="font-weight:900;color:var(--navy);font-size:7.8px">EXCEPTIONAL SERVICE</div><div style="font-size:7.4px;color:#666">We put you first.</div></div></div>
  <div class="brand-tab" style="left:413px;width:75px;height:68px"><span class="brand-name" style="font-size:10px">Lon Pakard</span></div>
  <div class="abs" style="left:0;top:198px;width:500px;height:38px;background:var(--yellow)"></div>
  <div class="abs script" style="left:12px;top:205px;font-size:24px;color:var(--navy)">Call Dane</div>
  <div class="abs" style="left:114px;top:205px;width:1px;height:24px;background:var(--navy)"></div>
  <div class="abs" style="left:128px;top:207px;display:flex;align-items:center;gap:6px">
    <span class="phone-dot" style="background:var(--dark);color:var(--yellow);width:20px;height:20px"><svg><use href="#phone"/></svg></span>
    <span style="font-weight:900;font-size:17px;color:#222">0491 570 156</span>
  </div>
  <div class="abs" style="left:282px;top:206px;width:218px;height:21px;background:var(--dark);border-radius:11px 0 0 11px;color:var(--yellow);font-weight:900;font-size:11.5px;display:flex;align-items:center;justify-content:center">YOUR PROPERTY OUR PRIORITY</div>
</section>

<!-- Flyer 4 back -->
<section class="card flyer-four-back" style="left:628px;top:902px">
  <div class="note-col" style="left:12px">
    <h5 class="num-head"><span class="num-sq">1</span><span>Getting<br>things fixed:</span></h5>
    <p style="margin-top:2px">One of the biggest advantages is that you can improve the condition of the property if you know there are things that can be fixed. This makes it a much better product to market.</p>
    <div style="height:1px;background:var(--yellow);margin:6px 0"></div>
    <h5 class="num-head"><span class="num-sq">2</span><span>Getting this reflected<br>in the report:</span></h5>
    <p style="margin-top:2px">Fixing issues means fixing them to the satisfaction of the building inspector. When this is done properly, the inspector can update his report to reflect the improved condition of the property, giving the owner more confidence in marketing and giving buyers more confidence in the property itself.</p>
  </div>
  <div class="abs" style="left:163px;top:12px;width:1px;height:180px;background:var(--yellow)"></div>
  <div class="note-col" style="left:171px;width:150px">
    <h5 class="num-head"><span class="num-sq">3</span><span>Making the report<br>available to buyers:</span></h5>
    <p style="margin-top:2px">Another big advantage of inspecting your property before marketing it is that the inspection report can then be available to buyers at the beginning of the campaign. This means buyers can carry out their checks faster and, usually, at a lower cost.</p>
    <h5 style="margin-top:8px">However it’s very important that this process is done professionally.</h5>
    <div class="callout"><svg style="color:var(--navy)"><use href="#house"/></svg><p><b style="color:#222">What if the property has serious issues?</b> Some issues can’t be fixed easily – like rising damp or wall cracks – but it’s much better to know what you’re dealing with and have a strategy for managing those issues with buyers.</p></div>
  </div>
  <div class="abs" style="left:328px;top:12px;width:1px;height:180px;background:var(--yellow)"></div>
  <div class="note-col" style="left:336px;width:152px">
    <p>For the example above, the owner could’ve addressed the issue before marketing. He could’ve had the pest infestation eliminated by a pest controller and had the timber damage assessed and repaired by a qualified tradesperson. Then the inspector could have attended the property to assess the condition again.</p>
    <h5 style="margin-top:8px">Always remember - if your listing is in good condition, why wouldn’t you want buyers to know that?</h5>
    <div class="callout"><svg style="color:var(--navy)"><use href="#doc"/></svg><p>If buyers can access better information about the property and get professional follow up support for a low fee, it’s likely to be one of the best ways to market a property.</p></div>
  </div>
  <div class="abs" style="left:0;top:203px;width:500px;height:33px;background:var(--yellow);display:flex;align-items:center;justify-content:center;gap:6px;color:var(--navy)">
    <span class="script" style="font-size:17px">Your property. Our priority.</span>
    <span style="width:1px;height:16px;background:var(--navy)"></span>
    <svg style="width:14px;height:14px"><use href="#house"/></svg>
    <span style="font-weight:900;font-size:12px">Let's achieve your next move together.</span>
  </div>
</section>
</body>
</html>
```